Design für Geburtskarte A6 hoch, Klappkarte
Zielgruppe
Ich bin Fotograf und habe mich auf Schwangerschafts- und Neugeborenenfotografie spezialisiert. Meine Zielgruppe sind schwangere Frauen im letzten Drittel der Schwangerschaft und frisch gewordene Eltern.
Aufgabenstellung
- sehr schlichtes Design, in der Anlage finden Sie zwei der meist verkauften Karten damit Sie sich vom Stil eine Vorstellung machen können
- Lieferung als offene Indesign 5.5 Datei (so das die Farben, Texte, .... angepasst werden können)
- 2-3 Bilder (querformat) sollen in das Design eingearbeitet werden können
- Die Karten werden von mir nachher als fertig gedruckte Karte an meine Kunden verkauft, dies bitte ich zu berücksichtigen
- ich möchte die Karten so nutzen können das sowohl Geburtskarten für Jungs wie auch für Mädels erstellt werden können
- Format: Din A6 (geschlossen 105x148mm), Klappkarte, hoch, 3mm Beschnitt

```html
<!DOCTYPE html>
<html lang="de">
<head>
<meta charset="utf-8">
<title>Geburtskarte Jonas</title>
<link rel="stylesheet" href="https://fonts.googleapis.com/css2?family=Josefin+Sans:wght@300;400&family=Dancing+Script:wght@600&display=swap">
<style>
  :root {
    --backdrop: #6c8497;
    --card-blue: #8fa6b5;
    --card-light: #eceeef;
    --frame-white: #f6f6f5;
    --photo-warm-1: #e9e1d9;
    --photo-warm-2: #d6c2b0;
    --photo-brown-1: #8a7358;
    --photo-brown-2: #c8ab92;
    --text-white: #ffffff;
    --text-dark: #2d3a44;
  }
  * { margin: 0; padding: 0; box-sizing: border-box; }
  html, body { width: 1200px; height: 820px; overflow: hidden; }
  body {
    background: var(--backdrop);
    font-family: "Josefin Sans", "Helvetica Neue", Arial, sans-serif;
    position: relative;
  }
  .card {
    position: absolute;
    top: 130px;
    width: 397px;
    height: 560px;
  }
  /* Front cover */
  .card-front {
    left: 170px;
    background: var(--card-light);
  }
  .card-front .cover-frame {
    position: absolute;
    inset: 18px;
    background: var(--frame-white);
    padding: 8px;
  }
  .card-front .cover-photo {
    width: 100%;
    height: 100%;
    background: linear-gradient(160deg, var(--photo-warm-1) 0%, var(--photo-warm-2) 55%, var(--photo-warm-1) 100%);
    position: relative;
  }
  .card-front .corner-accents {
    position: absolute;
    inset: 0;
    pointer-events: none;
  }
  .baby-name {
    position: absolute;
    left: 0; right: 0;
    bottom: 52px;
    text-align: center;
    font-family: "Dancing Script", cursive;
    font-weight: 600;
    font-size: 52px;
    color: var(--text-white);
    line-height: 1;
  }
  .birth-facts {
    position: absolute;
    left: 0; right: 0;
    bottom: 24px;
    text-align: center;
    font-weight: 300;
    font-size: 13px;
    letter-spacing: 0.5px;
    color: var(--text-white);
  }
  /* Back cover */
  .card-back {
    left: 630px;
    background: var(--card-blue);
  }
  .card-back .photo-band {
    position: absolute;
    left: 0; right: 0;
    top: 81px;
    height: 234px;
    background: var(--card-light);
    padding: 9px 9px;
  }
  .card-back .band-photo {
    width: 100%;
    height: 100%;
    background: radial-gradient(ellipse at 50% 60%, var(--photo-brown-2) 0%, var(--photo-brown-1) 75%);
  }
  .family-address {
    position: absolute;
    left: 0; right: 0;
    top: 340px;
    text-align: center;
    font-weight: 300;
    font-size: 14.5px;
    line-height: 21px;
    color: var(--text-white);
    font-style: normal;
  }
  .photo-credit {
    position: absolute;
    left: 0; right: 0;
    bottom: 10px;
    text-align: center;
    font-weight: 400;
    font-size: 8px;
    letter-spacing: 0.3px;
    color: var(--text-dark);
  }
</style>
</head>
<body>
  <section class="card card-front">
    <div class="cover-frame">
      <div class="cover-photo" role="img" aria-label="Foto: schlafendes Neugeborenes auf heller Strickdecke">
        <p class="baby-name">Jonas</p>
        <p class="birth-facts">51cm · 3450g · 03.09.2018 · 8:15</p>
      </div>
    </div>
    <svg class="corner-accents" viewBox="0 0 397 560" width="397" height="560" aria-hidden="true">
      <polygon points="0,0 118,0 0,100" fill="var(--card-blue)"/>
      <polygon points="397,560 279,560 397,455" fill="var(--card-blue)"/>
    </svg>
  </section>

  <section class="card card-back">
    <div class="photo-band">
      <div class="band-photo" role="img" aria-label="Foto: lächelndes Neugeborenes in brauner Felldecke"></div>
    </div>
    <address class="family-address">
      Familie Mustermann<br>
      Musterstraße 5a<br>
      87651 Musterstadt
    </address>
    <p class="photo-credit">FOTOS: WWW.BABYFOTOGRAF-LINDENAU.DE</p>
  </section>
</body>
</html>
```